wealth management firm, professional group, new model

we have a logo that works but we need a card, white background using our colors...clean look

our tag line if can be used in

Building Lasting Wealth Together

```html
<!DOCTYPE html>
<html lang="en">
<head>
<meta charset="utf-8">
<title>Astera Wealth Partners – Business Card</title>
<link href="https://fonts.googleapis.com/css2?family=Lato:wght@300;400;700&display=swap" rel="stylesheet">
<style>
  :root {
    --navy: #1a2e4f;
    --white: #ffffff;
    --backdrop: #ebebeb;
    --card-edge: #dcdcdc;
  }
  * { margin: 0; padding: 0; box-sizing: border-box; }
  html, body {
    width: 1200px; height: 1000px; overflow: hidden;
    background: var(--backdrop);
    font-family: "Lato", sans-serif;
  }
  .canvas { position: relative; width: 1200px; height: 1000px; }
  .card {
    position: absolute; left: 254px; width: 693px; height: 396px;
    border-radius: 22px; overflow: hidden;
  }
  .card--front { top: 78px; background: var(--navy); color: var(--white); }
  .card--back { top: 526px; background: var(--white); color: var(--navy); border: 1px solid var(--card-edge); }

  .contact { position: absolute; left: 50px; top: 54px; list-style: none; font-size: 16px; }
  .contact li { display: flex; align-items: flex-start; line-height: 21px; margin-bottom: 3px; }
  .contact li.contact__address { margin-bottom: 8px; }
  .contact li.contact__phone { font-size: 17.5px; }
  .contact svg { width: 14px; height: 14px; margin: 4px 9px 0 0; flex: none; fill: var(--white); }

  .identity { position: absolute; right: 55px; top: 50px; text-align: right; }
  .identity__name { font-size: 29px; font-weight: 700; letter-spacing: 0.01em; line-height: 34px; }
  .identity__title { font-size: 16.5px; line-height: 20px; }

  .brand { position: absolute; left: 0; right: 0; text-align: center; font-weight: 300; }
  .brand__name { top: 170px; font-size: 50px; letter-spacing: 0.48em; padding-left: 0.48em; line-height: 60px; }
  .brand__descriptor { top: 255px; font-size: 22px; letter-spacing: 0.13em; padding-left: 0.13em; }
  .brand__tagline { top: 339px; font-size: 18px; font-weight: 400; }
</style>
</head>
<body>
<main class="canvas">
  <section class="card card--front" aria-label="Business card front">
    <ul class="contact">
      <li class="contact__address">
        <svg viewBox="0 0 14 14"><path d="M7 0a5 5 0 0 0-5 5c0 3.6 5 9 5 9s5-5.4 5-9a5 5 0 0 0-5-5zm0 7a2 2 0 1 1 0-4 2 2 0 0 1 0 4z"/></svg>
        <span>Street Address Here, City<br>State, Country, ZIP 123</span>
      </li>
      <li class="contact__phone">
        <svg viewBox="0 0 14 14"><path d="M3 1l2 3-1.3 1.3a8 8 0 0 0 5 5L10 9l3 2-1.2 2.2C6.5 13.5 0.5 7.5 0.8 2.2z"/></svg>
        <span>(123) 456-7890</span>
      </li>
      <li class="contact__phone">
        <svg viewBox="0 0 14 14"><path d="M4 0h6a1 1 0 0 1 1 1v12a1 1 0 0 1-1 1H4a1 1 0 0 1-1-1V1a1 1 0 0 1 1-1zm.6 1.6v9h4.8v-9z"/></svg>
        <span>(123) 456-7890</span>
      </li>
      <li class="contact__phone">
        <svg viewBox="0 0 14 14"><path d="M3 0h8v4H3zM1 5h12a1 1 0 0 1 1 1v5h-3v3H3v-3H0V6a1 1 0 0 1 1-1zm3.5 5v2.5h5V10z"/></svg>
        <span>(123) 456-7890</span>
      </li>
      <li>
        <svg viewBox="0 0 14 14"><path d="M1 3h12v8H1zM1.5 3.5 7 8l5.5-4.5" stroke="#1a2e4f" stroke-width="1"/></svg>
        <span>info@yourwebsitehere.com</span>
      </li>
      <li>
        <svg viewBox="0 0 14 14"><circle cx="7" cy="7" r="6.5"/><path d="M3 5c2 0 2 2 3.5 2S7 10 5.5 12M9 2c-1 2 1 3 3 3" stroke="#1a2e4f" stroke-width="1.3" fill="none"/></svg>
        <span>yourwebsitehere.com</span>
      </li>
    </ul>
    <div class="identity">
      <h1 class="identity__name">DANIEL REYES</h1>
      <p class="identity__title">Founder &amp; CEO</p>
    </div>
  </section>

  <section class="card card--back" aria-label="Business card back">
    <p class="brand brand__name">ASTERA</p>
    <p class="brand brand__descriptor">WEALTH PARTNERS</p>
    <p class="brand brand__tagline">Building Lasting Wealth Together</p>
  </section>
</main>
</body>
</html>
```